Falkrin homes and renovations business card design.

Would like some new card designs utilizing my new logo that look professional. I am open to different colors on the logo or utilize the same ones we have. I like the original concept but would like to see some fresh ideas and build on what we have already done.

Target Market(s)

Custom home building industry, Real estate sales, Renovation projects.

Industry/Entity Type

Home Builder

Contact Information for Business Card

Falkrin Homes and Renovations
2871 96th Avenue
Frank, Alberta
T2R3W8
Home : 403- 718-4063 Cell: 403- 294-5170

My info is : Dax Falkrin, President and CEO
email: falkrinhomes@maildrop-example.net
Website: falkrinhomes-example.com
websit

Requirements
Must have
• Must Use my new logo design. I am open to different colors on the logo or utilize the same ones in the existing design. I can upload the original logo design if needed.

```html
<!DOCTYPE html>
<html lang="en">
<head>
<meta charset="utf-8">
<title>Falkrin Homes and Renovations – Business Card</title>
<link href="https://fonts.googleapis.com/css2?family=Exo+2:wght@400;700&family=Open+Sans:wght@600&display=swap" rel="stylesheet">
<style>
  :root {
    --stage: #2b2b2d;
    --card: #1c1c1d;
    --card-edge: #141415;
    --gold: #f6b713;
    --logo-gold: #c99a31;
    --ink: #f2f2f2;
    --skyline-top: #2a2a2b;
    --skyline-bottom: #1c1c1d;
  }
  * { margin: 0; padding: 0; box-sizing: border-box; }
  html, body { width: 1200px; height: 1000px; overflow: hidden; }
  body { background: var(--stage); font-family: "Exo 2", sans-serif; position: relative; }

  .card {
    position: absolute;
    width: 620px;
    height: 354px;
    background: var(--card);
    box-shadow: 0 6px 24px rgba(0,0,0,.45);
    border: 1px solid var(--card-edge);
    overflow: hidden;
  }

  /* Back of card */
  .card-back { left: 420px; top: 70px; }
  .card-back .skyline {
    position: absolute;
    left: 90px; right: 50px; top: 0; bottom: 0;
    background: linear-gradient(to bottom, var(--skyline-top), var(--skyline-bottom));
  }
  .card-back .brand {
    position: absolute;
    left: 0; right: 0; top: 140px;
    text-align: center;
  }
  .card-back .web {
    position: absolute;
    left: 0; right: 0; bottom: 34px;
    display: flex; justify-content: center; align-items: center; gap: 10px;
    color: var(--ink); font-size: 15px; letter-spacing: 1.5px;
  }

  .brand-name {
    font-family: "Open Sans", sans-serif;
    font-weight: 600;
    color: var(--logo-gold);
    font-size: 19px;
    line-height: 1.25;
    text-transform: uppercase;
    letter-spacing: .5px;
  }

  /* Front of card */
  .card-front { left: 160px; top: 470px; }
  .holder { position: absolute; left: 40px; top: 38px; }
  .holder-name {
    color: var(--gold); font-weight: 700; font-size: 32px;
    letter-spacing: 2px; text-transform: uppercase; line-height: 1;
  }
  .holder-title { color: var(--ink); font-size: 17px; margin-top: 4px; }

  .card-front .brand {
    position: absolute; right: 40px; top: 112px; width: 200px; text-align: center;
  }

  .contacts { position: absolute; left: 40px; top: 218px; list-style: none; }
  .contacts li {
    display: flex; align-items: center; gap: 12px;
    color: var(--ink); font-size: 16px; letter-spacing: .8px; line-height: 21px;
  }
  .contacts svg { width: 13px; height: 13px; flex: none; }

  .address {
    position: absolute; right: 40px; bottom: 32px;
    color: var(--ink); font-size: 16px; letter-spacing: 1px; text-align: right; line-height: 22px;
  }
</style>
</head>
<body>

  <section class="card card-back">
    <div class="skyline" role="img" aria-label="Faint city skyline of tall buildings behind the company name"></div>
    <div class="brand"><p class="brand-name">Falkrin Homes<br>and Renovations</p></div>
    <p class="web">
      <svg width="14" height="14" viewBox="0 0 14 14" fill="none" stroke="var(--gold)" stroke-width="2"><circle cx="8" cy="6" r="4.5"/><line x1="4.8" y1="9.2" x2="1" y2="13"/></svg>
      www.falkrinhomes-example.com
    </p>
  </section>

  <section class="card card-front">
    <div class="holder">
      <h1 class="holder-name">Dax Falkrin</h1>
      <p class="holder-title">President and CEO</p>
    </div>

    <div class="brand"><p class="brand-name">Falkrin Homes<br>and Renovations</p></div>

    <ul class="contacts">
      <li>
        <svg viewBox="0 0 14 14" fill="var(--gold)"><path d="M3 1l2.5 3-1.3 1.5c.8 1.8 2.5 3.5 4.3 4.3L10 8.5l3 2.5-1.5 2C6 13 1 8 1 2.5z"/></svg>
        403 718 4063
      </li>
      <li>
        <svg viewBox="0 0 14 14" fill="none" stroke="var(--gold)" stroke-width="1.4"><rect x="3.5" y="1" width="7" height="12" rx="1"/><line x1="6" y1="11" x2="8" y2="11"/></svg>
        403 294 5170
      </li>
      <li>
        <svg viewBox="0 0 14 14" fill="var(--gold)"><path d="M1 3h12v8H1z"/><path d="M1 3l6 5 6-5" fill="none" stroke="var(--card)" stroke-width="1.2"/></svg>
        falkrinhomes@maildrop-example.net
      </li>
      <li>
        <svg viewBox="0 0 14 14" fill="none" stroke="var(--gold)" stroke-width="2"><circle cx="8" cy="6" r="4.5"/><line x1="4.8" y1="9.2" x2="1" y2="13"/></svg>
        www.falkrinhomes-example.com
      </li>
    </ul>

    <address class="address" style="font-style:normal">
      2871 96th Avenue<br>Frank, Alberta
    </address>
  </section>

</body>
</html>
```